Local Chiropractor Needs Up Scale Webdesign

This website needs to have an upscale look with a very modern feel. Below is the information and websites to reference

Add Logo that is attached

Build a color scheme similar to this website image titled "chiro-1"

Must Include these pages in a horizontal menu bar in this order:
Home, Meet Our Staff, Patient Testimonials, Videos, Work Place Wellness, Contact

Build a "classy looking" Make An Appointment Button into the header with the contact info below

Phone Number:
555-314-2719

Address:
3168 Pelham Orchard Lane, #240
Lakeview Falls, MN 55390

This website needs 4 rotating banners. Please reference a layout similar to this for the banners: http://drmorlatz.example/. However design it nicer than this website, this website is very boring and doesn't flow with the colors properly

Below are the description for each banner

Rotating Banner #1
Use Image: Pediatrics
Two lines of text. First line title line, second description. Use Latin text for fill

Rotating Banner #2
Use Image: Aging Gracefully

Rotating Banner #3
Use Image: Pregnancy

Rotating Banner #4
Use Image: Athletics

I'd like to see a free consultation box similar to the "chiro-1" image. Fields to include are: First Name, Last Name, Phone Number, Comments.

For the body, please fill it with latin text. Please design a professional body layout. You can include a box in the right column for the hours

Office Hours
Monday: 8:00-11:00, 2:00-5:00
Tuesday: 8:30-11:00, 2:00-5:30
Wednesday: 8:00-11:00, 2:00-5:00
Thursday: 10:00-12:00, 2:30-5:00
Friday: 8:00-10:00, 1:00-5:00
Saturday: Closed
Sunday: Closed

For the footer please design something similar to the: http://drmorlatz.example/

Also include in the Footer: Powered by Brightline Site Works

```html
<!DOCTYPE html>
<html lang="en">
<head>
<meta charset="utf-8">
<title>Evergreen Spine Chiropractic</title>
<link href="https://fonts.googleapis.com/css2?family=Lato:ital,wght@0,400;0,700;0,900;1,700;1,900&display=swap" rel="stylesheet">
<style>
:root{
  --dark:#2c2c2c;
  --dark-2:#383838;
  --green:#8cc63f;
  --green-deep:#6ea822;
  --text:#666;
  --heading:#222;
  --line:#e3e3e3;
  --white:#fff;
}
*{box-sizing:border-box;margin:0;padding:0}
html,body{width:692px;height:1200px;overflow:hidden;background:#fff}
body{font-family:'Lato',sans-serif;color:var(--text)}
.page{position:relative;width:807px;height:1400px;transform:scale(.8575);transform-origin:0 0}
.abs{position:absolute}
a{color:inherit;text-decoration:none}

/* header */
.topbar{left:0;top:0;width:807px;height:75px;background:var(--dark)}
.brand{left:108px;top:22px;display:flex;align-items:center;gap:6px;color:var(--white);font-size:11px;font-weight:700;line-height:1;white-space:nowrap}
.brand-dot{width:14px;height:14px;border-radius:50%;background:var(--green)}
.contact-item{top:19px;display:flex;gap:10px;align-items:flex-start}
.contact-item svg{width:16px;height:16px;fill:#777;margin-top:2px}
.contact-item b{display:block;color:var(--white);font-size:7px;font-weight:700}
.contact-item span{display:block;color:#888;font-size:6.5px;margin-top:3px}
.btn-appt{left:598px;top:15px;width:101px;height:26px;background:linear-gradient(#93cc45,var(--green-deep));color:var(--white);font-size:7px;font-weight:900;display:flex;align-items:center;justify-content:center;border-radius:2px}

.nav{left:108px;top:57px;width:591px;height:38px;background:linear-gradient(#fff,#ececec);box-shadow:0 2px 4px rgba(0,0,0,.2);display:flex;justify-content:center;z-index:3}
.nav a{position:relative;padding:0 7px;font-size:6.5px;color:#555;text-transform:uppercase;line-height:38px;border-right:1px solid #ddd}
.nav a:last-child{border-right:0}
.nav a::before{content:"";position:absolute;left:50%;top:4px;margin-left:-2px;border:2px solid transparent;border-top-color:#888}
.nav a.active{color:#333;font-weight:700}
.nav a.active::after{content:"";position:absolute;left:0;right:0;bottom:0;height:3px;background:var(--green)}

/* hero */
.hero{left:0;top:75px;width:807px;height:278px;background:linear-gradient(100deg,#f1ece8 0%,#e8e3e6 30%,#f3f3f5 55%,#e9dfd8 75%,#f6f6f8 100%)}
.caption{left:108px;top:157px;width:253px;height:134px;background:rgba(30,30,30,.78);padding:5px}
.caption-inner{border:1px solid rgba(255,255,255,.6);height:100%;padding:10px 10px}
.caption h1{color:var(--white);font-size:20px;font-weight:700;margin-bottom:9px}
.caption p{color:#ddd;font-size:7.5px;line-height:14px}
.arrows{display:flex;gap:5px;margin-top:8px}
.arrows span{width:25px;height:25px;background:linear-gradient(#93cc45,var(--green-deep));display:flex;align-items:center;justify-content:center}
.arrows svg{width:8px;height:8px;stroke:#fff;stroke-width:2;fill:none}

.band{left:0;top:353px;width:807px;height:50px;background:var(--dark)}
.band-text{left:108px;top:372px;color:var(--white);font-size:8.5px;font-weight:900;font-style:italic}
.btn-outline{left:622px;top:367px;width:77px;height:22px;border:1px solid #ccc;color:var(--white);font-size:7px;font-weight:700;display:flex;align-items:center;justify-content:center;gap:4px}

/* main */
.section-title{font-size:9px;color:var(--heading)}
.section-sub{font-size:5px;color:#999;margin-top:1px}
.rule{height:1px;background:var(--line);margin-top:9px;position:relative}
.rule::before{content:"";position:absolute;left:0;top:-1px;width:24px;height:2px;background:var(--green)}
.copy{font-size:6.6px;line-height:12.5px;color:#777}
.about{left:108px;top:442px;width:387px}
.about .copy{margin-top:9px}
.about .copy + .copy{margin-top:12px}
.ticks{left:108px;top:613px;list-style:none}
.ticks li{display:flex;gap:4px;align-items:center;font-size:6.4px;font-weight:700;color:#333;height:18.5px}
.ticks svg{width:8px;height:8px;stroke:var(--green);stroke-width:2;fill:none}

.card{top:708px;width:187px}
.card-photo{height:111px}
.card h3{font-size:8.5px;font-weight:400;color:var(--heading);margin-top:10px}
.card h3.hl{color:var(--green)}
.card .rule{margin-top:9px}
.card .copy{margin-top:7px}
.read-more{display:flex;gap:3px;align-items:center;font-size:6.5px;font-weight:700;color:#333;margin-top:8px}
.read-more.hl{color:var(--green)}

/* sidebar */
.hours{left:512px;top:443px;width:187px;height:149px;border:1px solid #ddd}
.panel-head{height:31px;background:var(--dark);color:var(--white);font-size:8.5px;font-weight:700;display:flex;align-items:center;justify-content:center}
.hours dl{display:grid;grid-template-columns:1fr auto;padding:6px 9px;font-size:6px;color:#555;row-gap:8.5px}
.hours dd{text-align:right}
.hours .closed{color:var(--green)}

.consult{left:512px;top:606px;width:187px;height:310px;border:1px solid #ddd}
.consult-head{position:relative;height:55px;background:var(--dark);text-align:center;padding-top:8px}
.consult-head::after{content:"";position:absolute;left:0;top:54px;border-left:93px solid transparent;border-right:93px solid transparent;border-top:16px solid var(--dark)}
.consult-head .small{color:var(--green);font-size:6.5px}
.consult-head .big{color:var(--white);font-size:10px;font-weight:700;margin:5px 0 4px}
.form{padding:25px 9px 0}
.form h4{font-size:8px;font-weight:400;color:#222;margin-bottom:12px}
.form label{display:block;font-size:6.2px;color:#333;margin-bottom:4px}
.field{height:15px;border:1px solid #ddd;margin-bottom:13px}
.field.focus{border-color:var(--green)}
.field.area{height:50px;margin-bottom:10px}
.btn-submit{width:64px;height:21px;background:linear-gradient(#93cc45,var(--green-deep));color:var(--white);font-size:7px;font-weight:700;display:flex;align-items:center;justify-content:center;gap:3px}

/* newsletter */
.news{left:108px;top:957px;width:591px;height:151px;background:repeating-linear-gradient(45deg,#e6e6e6 0 3px,#fff 3px 6px);padding:10px}
.news-inner{background:var(--white);height:100%;text-align:center;padding-top:24px}
.news h2{font-size:13.5px;font-weight:700;color:#222}
.news p{font-size:7px;color:#666;margin-top:6px}
.news-form{display:flex;justify-content:center;margin-top:24px}
.news-field{width:151px;height:23px;border:1px solid #ddd;display:flex;align-items:center;gap:8px;padding-left:9px;font-size:6px;font-style:italic;color:#888}
.news-field svg{width:8px;height:8px;stroke:#777;fill:none}
.btn-sub{margin-left:5px;width:62px;height:23px;background:linear-gradient(#93cc45,var(--green-deep));color:var(--white);font-size:7px;font-weight:700;display:flex;align-items:center;justify-content:center}

/* footer */
.foot-top{left:0;top:1148px;width:807px;height:42px;background:var(--dark-2)}
.social{left:557px;top:1158px;display:flex;gap:4px}
.social span{width:20px;height:20px;background:#2a2a2a;border:1px solid #555}
.social span.on{background:var(--green);border-color:var(--green)}
.foot{left:0;top:1190px;width:807px;height:170px;background:var(--dark)}
.foot-col{top:1218px;color:#bbb}
.foot-col h5{font-size:7.5px;font-weight:700;color:#ddd;text-align:center;margin-bottom:22px}
.foot-col .copy{color:#666;font-size:6.3px;line-height:12.3px}
.foot-links{display:flex;font-size:6.5px;color:#ddd;margin-top:12px}
.foot-links a{padding:0 9px;border-left:1px solid #555}
.foot-links a:first-child{padding-left:0;border-left:0}
.foot-links .hl{color:var(--green)}
.map{width:183px;height:76px;background:linear-gradient(135deg,#dcdcdc,#c9c9c9);border:2px solid #eee}
.touch b{display:block;font-size:6.5px;color:#eee;text-align:center;margin-bottom:11px}
.touch li{list-style:none;display:flex;align-items:center;gap:8px;font-size:6.3px;color:#aaa;height:15px;padding-left:38px}
.touch li svg{width:7px;height:7px;fill:#aaa}
.touch .hl{color:var(--green)}
.bottombar{left:0;top:1360px;width:807px;height:40px;background:var(--green);color:var(--white);font-size:6.5px;font-weight:700}
.bottombar .powered{position:absolute;left:108px;top:15px}
.bottom-links{position:absolute;right:152px;top:15px;display:flex}
.bottom-links a{padding:0 8px;border-left:1px solid rgba(255,255,255,.6)}
.bottom-links a:first-child{border-left:0}
.to-top{position:absolute;left:668px;top:10px;width:31px;height:20px;border:1px solid var(--white);display:flex;align-items:center;justify-content:center}
.to-top svg{width:7px;height:7px;stroke:#fff;stroke-width:2;fill:none}
</style>
</head>
<body>
<div class="page">

  <header>
    <div class="abs topbar"></div>
    <div class="abs brand"><span class="brand-dot"></span>Evergreen Spine Chiropractic</div>
    <div class="abs contact-item" style="left:370px">
      <svg viewBox="0 0 24 24"><path d="M6.6 10.8a15 15 0 0 0 6.6 6.6l2.2-2.2c.3-.3.7-.4 1-.2 1.1.4 2.3.6 3.6.6.6 0 1 .4 1 1V20c0 .6-.4 1-1 1A17 17 0 0 1 3 4c0-.6.4-1 1-1h3.5c.6 0 1 .4 1 1 0 1.3.2 2.5.6 3.6.1.3 0 .7-.2 1z"/></svg>
      <div><b>555-314-2719</b><span>info@example.com</span></div>
    </div>
    <div class="abs contact-item" style="left:470px">
      <svg viewBox="0 0 24 24"><path d="M12 3 2 12h3v8h5v-6h4v6h5v-8h3z"/></svg>
      <div><b>Lakeview Falls, MN 55390</b><span>3168 Pelham Orchard Lane, #240</span></div>
    </div>
    <a class="abs btn-appt" href="#">MAKE AN APPOINTMENT</a>
    <nav class="abs nav">
      <a href="#">Home</a><a class="active" href="#">Meet Our Staff</a><a href="#">Patient Testimonials</a><a href="#">Videos</a><a href="#">Work Place Wellness</a><a href="#">Contact</a>
    </nav>
  </header>

  <section>
    <div class="abs hero" role="img" aria-label="Photo of a little girl lifting a pregnant mother's shirt to see her belly"></div>
    <div class="abs caption"><div class="caption-inner">
      <h1>Your Title Goes Here</h1>
      <p>Lorem ipsum dolor sit amet, consectetur adipisicing elit, sed do eiusmod tempor incididunt ut labore et dolore magna aliqua.</p>
      <div class="arrows">
        <span><svg viewBox="0 0 10 10"><path d="M6.5 1.5 3 5l3.5 3.5"/></svg></span>
        <span><svg viewBox="0 0 10 10"><path d="M3.5 1.5 7 5 3.5 8.5"/></svg></span>
      </div>
    </div></div>
    <div class="abs band"></div>
    <p class="abs band-text">DONEC SUSCIPIT VEHICULA TURPIS SED LUTPAT QUISQUE VITAE QUAM NEQUE?</p>
    <a class="abs btn-outline" href="#">Contact Us <svg width="8" height="6" viewBox="0 0 8 6" fill="none" stroke="#fff"><rect x=".5" y=".5" width="7" height="5"/><path d="M.5.5 4 3.5 7.5.5"/></svg></a>
  </section>

  <main>
    <div class="abs about">
      <h2 class="section-title">Hello Dear Visitor</h2>
      <p class="section-sub">This is an About Us Text</p>
      <div class="rule"></div>
      <p class="copy">Pellentesque habitant morbi tristique senectus et netus et malesuada fames ac turpis egestas. Donec faucibus aliquet dui, nec congue orci sagittis eget. Sed sit amet augue id nisi fringilla elementum ut nec augue. Fusce ultrices convallis enim eu interdum. Nam libero neque, congue id nisl vel, sagittis malesuada ex. Ut vel arcu sed ligula condimentum con sequat sed vehicula purus. Donec eu erat pharetra, euismod justo id, volutpat orci. Etiam ac tortor ut urna egestas cursus vel nec nisi. Vivamus molestie nec magna sit amet rutrum.</p>
      <p class="copy">Nullam maximus tincidunt metus, quis tempus libero vulputate non. Ut vitae aliquam urna, pharetra elementum ipsum. Phasellus maximus dolor orci. Pellentesque leo tortor, hendrerit sit amet rutrum. Imperdiet vel ligula. Cum sociis natoque penatibus et magnis dis parturient montes, nascetur ridiculus mus.</p>
    </div>
    <ul class="abs ticks">
      <li><svg viewBox="0 0 10 10"><path d="M1.5 5.5 4 8l5-6"/></svg>SED NON MASSA SIT AMET ENIM FEUGIAT BIBENDUM A ET ARCU</li>
      <li><svg viewBox="0 0 10 10"><path d="M1.5 5.5 4 8l5-6"/></svg>CRAS ACCUMSAN TRISTIQUE EUISMOD. IN AC DIAM ET NULLA HENDRERIT</li>
      <li><svg viewBox="0 0 10 10"><path d="M1.5 5.5 4 8l5-6"/></svg>FUSCE EU TELLUS PHARETRA, ULTRICES DUI VITAE RHONCUS</li>
      <li><svg viewBox="0 0 10 10"><path d="M1.5 5.5 4 8l5-6"/></svg>NIBH. QUISQUE ID QUAM VELIT. MORBI MALESUADA LOREM A NISL MOLLIS TEMPUS</li>
    </ul>

    <article class="abs card" style="left:108px">
      <div class="card-photo" role="img" aria-label="Photo of two skiers descending a snowy slope" style="background:linear-gradient(160deg,#c9d2dc,#eef1f4 60%,#d7dde3)"></div>
      <h3>Title Goes Here</h3><p class="section-sub">This is Subtitle</p>
      <div class="rule"></div>
      <p class="copy">Placerat dapibus. Etiam ultrices nulla sed leo malesuada commodo bibendum orci vi verra. Sed rutrum dapibus feugiat. Iasellus et congue arcu.</p>
      <a class="read-more" href="#">Read More <svg width="7" height="7" viewBox="0 0 10 10" fill="none" stroke="#333"><path d="M2 5h6M5.5 2.5 8 5 5.5 7.5"/></svg></a>
    </article>
    <article class="abs card" style="left:310px">
      <div class="card-photo" role="img" aria-label="Green-tinted photo of a little girl with her pregnant mother" style="background:linear-gradient(135deg,#a9d65e,#8cc63f 60%,#9bcf50)"></div>
      <h3 class="hl">Title Goes Here</h3><p class="section-sub">This is Subtitle</p>
      <div class="rule"></div>
      <p class="copy">Placerat dapibus. Etiam ultrices nulla sed leo malesuada commodo bibendum orci vi verra. Sed rutrum dapibus feugiat. Iasellus et congue arcu.</p>
      <a class="read-more hl" href="#">Read More <svg width="7" height="7" viewBox="0 0 10 10" fill="none" stroke="#8cc63f"><path d="M2 5h6M5.5 2.5 8 5 5.5 7.5"/></svg></a>
    </article>

    <aside>
      <div class="abs hours">
        <div class="panel-head">OPENING HOURS</div>
        <dl>
          <dt>Monday</dt><dd>8:00-11:00, 14:00-17:00</dd>
          <dt>Tuesday</dt><dd>8:30-11:00, 14:00-17:30</dd>
          <dt>Wednesday</dt><dd>8:00-11:00, 14:00-17:00</dd>
          <dt>Thursday</dt><dd>10:00-12:00, 14:30-17:00</dd>
          <dt>Friday</dt><dd>8:00-10:00, 13:00-17:00</dd>
          <dt class="closed">Saturday</dt><dd class="closed">Closed</dd>
          <dt class="closed">Sunday</dt><dd class="closed">Closed</dd>
        </dl>
      </div>
      <div class="abs consult">
        <div class="consult-head">
          <p class="small">CONTACT US NOW &amp; GET YOUR</p>
          <p class="big">FREE CONSULTATION</p>
          <p class="small">TODAY !</p>
        </div>
        <div class="form">
          <h4>WELLNESS BEGINS HERE</h4>
          <label>First Name</label><div class="field"></div>
          <label>Last Name</label><div class="field focus"></div>
          <label>Phone Number</label><div class="field"></div>
          <label>Comments</label><div class="field area"></div>
          <a class="btn-submit" href="#">Submit <svg width="7" height="7" viewBox="0 0 10 10" fill="none" stroke="#fff"><path d="M2 5h6M5.5 2.5 8 5 5.5 7.5"/></svg></a>
        </div>
      </div>
    </aside>

    <section class="abs news">
      <div class="news-inner">
        <h2>NEWSLETTER SUBSCRIPTION</h2>
        <p>Subscribe and be the first one who is getting the latest news &amp; notes! We promise to keep your mails safe, NO SPAMS!</p>
        <div class="news-form">
          <div class="news-field"><svg viewBox="0 0 10 10"><path d="M1 9h8M2 7l5-5 1.5 1.5-5 5H2z"/></svg>Enter Your Full Name</div>
          <div class="news-field"><svg viewBox="0 0 10 10"><rect x="1" y="2" width="8" height="6"/><path d="M1 2l4 3.5L9 2"/></svg>Enter Your Email Address</div>
          <a class="btn-sub" href="#">Subscribe</a>
        </div>
      </div>
    </section>
  </main>

  <footer>
    <div class="abs foot-top"></div>
    <div class="abs brand" style="top:1163px;font-size:9px"><span class="brand-dot" style="width:11px;height:11px"></span>Evergreen Spine Chiropractic</div>
    <div class="abs social" aria-label="Social links"><span></span><span class="on"></span><span></span><span></span><span></span><span></span></div>
    <div class="abs foot"></div>

    <div class="abs foot-col" style="left:108px;width:188px">
      <h5>- ABOUT US -</h5>
      <p class="copy">Phasellus rhoncus sapien ipsum, at sollicitudin nunc rhoncus quis. Mauris gravida neque elementum est imperdiet, non vehicula risus finibus. Vivamus faucibus aliquet leo vitae laoreet. Cras commodo velit metus.</p>
      <div class="foot-links"><a href="#">Privacy Policy</a><a class="hl" href="#">Terms and Conditions</a><a href="#">FAQ</a></div>
    </div>
    <div class="abs foot-col" style="left:312px;width:183px">
      <h5>- WE ARE HERE -</h5>
      <div class="map" role="img" aria-label="Street map showing the clinic location"></div>
    </div>
    <div class="abs foot-col touch" style="left:510px;width:190px">
      <h5>- GET IN TOUCH -</h5>
      <b>3168 Pelham Orchard Lane, #240 Lakeview Falls, MN 55390</b>
      <ul>
        <li><svg viewBox="0 0 24 24"><path d="M6.6 10.8a15 15 0 0 0 6.6 6.6l2.2-2.2c.3-.3.7-.4 1-.2 1.1.4 2.3.6 3.6.6.6 0 1 .4 1 1V20c0 .6-.4 1-1 1A17 17 0 0 1 3 4c0-.6.4-1 1-1h3.5c.6 0 1 .4 1 1 0 1.3.2 2.5.6 3.6.1.3 0 .7-.2 1z"/></svg>+1 555-314-2719</li>
        <li><svg viewBox="0 0 24 24"><path d="M6 3h12v5H6zM3 9h18v8h-3v4H6v-4H3z"/></svg>+1 555-314-2719</li>
        <li><svg viewBox="0 0 24 24"><path d="M2 5h20v14H2zm2 2v1l8 5 8-5V7z"/></svg><span class="hl">info@example.com</span></li>
        <li><svg viewBox="0 0 24 24"><path d="M12 2a7 7 0 0 0-7 7c0 5 7 13 7 13s7-8 7-13a7 7 0 0 0-7-7zm0 9.5A2.5 2.5 0 1 1 12 6.5a2.5 2.5 0 0 1 0 5z"/></svg>see in large map</li>
      </ul>
    </div>

    <div class="abs bottombar">
      <p class="powered">Powered by Brightline Site Works © Copyright 2015</p>
      <nav class="bottom-links"><a href="#">Home</a><a href="#">Meet Our Staff</a><a href="#">Patient Testimonials</a><a href="#">Videos</a><a href="#">Work Place Wellness</a><a href="#">Contact</a></nav>
      <a class="to-top" href="#"><svg viewBox="0 0 10 10"><path d="M2 6.5 5 3.5 8 6.5"/></svg></a>
    </div>
  </footer>

</div>
</body>
</html>
```